Namecard Designs+Logo for a High End Automobile Company

We need a new business card for our company called Nordel Motorwerk.

www.nordelmotorwerk.example.sg
Our new website will be up in 2.5 months time.

We sell used and brand new continental cars like Valcrest, KTR, Almira, Dunvale and etc. Currently we are operating from 2 offices in Singapore and United Kingdom.

We want a design which is serious. We are open to colours but try to keep it at a maximum of 3 colours.

We prefer something simple and minimal. We are open to 2 sides printing or even 2 sided namecards. Both UK and Singapore company offices address must be in; either side by side, front and back, or even 2 sided cards.

The logo can be a text logo, emblem, abstract, pictorial or combination.

We are printing with Printlyx.com so please kindly follow the printing guideline.

http://uk.printlyx.example/help/faq/templates-and-guidelines.html

Rich and Car Enthusiasts

Printing

• Our 2 offices; UK and Singapore.

Our slogan which is " The Automobile Specialist"
• Not more than 3 colours

```html
<!DOCTYPE html>
<html lang="en">
<head>
<meta charset="utf-8">
<title>Nordel Motorwerk – Business Cards</title>
<link rel="stylesheet" href="https://fonts.googleapis.com/css2?family=Open+Sans:ital,wght@0,700;1,600&family=Crimson+Text&display=swap">
<style>
  :root {
    --page: #ffffff;
    --card-base: #dcd6cf;
    --card-light: #ebe6e0;
    --brand-blue: #2a8fd0;
  }
  html, body {
    margin: 0;
    width: 1200px;
    height: 900px;
    overflow: hidden;
    background: var(--page);
  }
  .canvas {
    position: relative;
    width: 1200px;
    height: 900px;
  }
  .card {
    position: absolute;
    width: 550px;
    height: 360px;
    overflow: hidden;
    background: var(--card-base);
    color: var(--brand-blue);
  }
  .card--front { left: 346px; top: 64px; }
  .card--back  { left: 350px; top: 492px; }
  .card-shapes {
    position: absolute;
    inset: 0;
  }
  .card-shapes .light { fill: var(--card-light); }

  .brand {
    position: absolute;
    left: 440px;
    top: 38px;
    transform: translateX(-50%);
    display: flex;
    flex-direction: column;
    align-items: center;
    gap: 14px;
  }
  .brand-mark {
    width: 66px;
    height: 66px;
    border: 7px solid var(--brand-blue);
    border-radius: 50%;
    box-sizing: border-box;
  }
  .brand-name {
    font-family: "Open Sans", sans-serif;
    font-weight: 700;
    font-size: 17px;
    white-space: nowrap;
    color: var(--brand-blue);
  }

  .slogan {
    position: absolute;
    left: 218px;
    top: 210px;
    transform: translate(-50%, -50%) rotate(-40deg);
    font-family: "Open Sans", sans-serif;
    font-style: italic;
    font-weight: 600;
    font-size: 22px;
    white-space: nowrap;
    margin: 0;
  }

  .office {
    position: absolute;
    transform: translate(-50%, -50%) rotate(-45deg);
    font-family: "Crimson Text", serif;
    font-style: normal;
    line-height: 1.2;
    white-space: nowrap;
  }
  .office--uk { left: 162px; top: 100px; }
  .office--sg { left: 318px; top: 286px; }
  .office-title { font-size: 16px; display: block; }
  .office-line { font-size: 11.5px; display: block; }

  .person {
    position: absolute;
    right: 360px;
    top: 230px;
    font-family: "Crimson Text", serif;
    text-align: right;
  }
  .person-name { font-size: 24px; display: block; line-height: 1.1; white-space: nowrap; }
  .person-role { font-size: 12.5px; display: block; }
</style>
</head>
<body>
<main class="canvas">

  <section class="card card--front" aria-label="Card front">
    <svg class="card-shapes" width="550" height="360" viewBox="0 0 550 360" aria-hidden="true">
      <path class="light" d="M0 0 H300 L140 150 Q125 164 110 150 L0 44 Z"/>
      <path class="light" d="M160 360 L340 180 Q355 166 370 180 L550 340 V360 Z"/>
    </svg>
    <div class="brand">
      <span class="brand-mark"></span>
      <span class="brand-name">Nordel Motorwerk</span>
    </div>
    <p class="slogan">The Automobile Specialist</p>
  </section>

  <section class="card card--back" aria-label="Card back">
    <svg class="card-shapes" width="550" height="360" viewBox="0 0 550 360" aria-hidden="true">
      <path class="light" d="M0 0 H300 L125 158 Q110 172 95 158 L0 64 Z"/>
      <path class="light" d="M170 360 L335 180 Q350 166 365 180 L550 330 V360 Z"/>
    </svg>
    <div class="brand">
      <span class="brand-mark"></span>
      <span class="brand-name">Nordel Motorwerk</span>
    </div>

    <address class="office office--uk">
      <span class="office-title">UK Office</span>
      <span class="office-line">12 Harrow Lane Kingsmere</span>
      <span class="office-line">mobile : 0455 218374</span>
      <span class="office-line">email : sales@nordel.example</span>
    </address>

    <div class="person">
      <span class="person-name">Adrian Kessler</span>
      <span class="person-role">Managing Director</span>
    </div>

    <address class="office office--sg">
      <span class="office-title">Singapore Office</span>
      <span class="office-line">12 Harrow Lane Kingsmere</span>
      <span class="office-line">mobile : 0455 218374</span>
      <span class="office-line">email : sales@nordel.example</span>
    </address>
  </section>

</main>
</body>
</html>
```